Website design for Puddle Jump Kidscare

I need a website designed for my daycare business, Puddle Jump Kidscare, now that I have a new logo. My former website was ok but simple and I did not have a logo yet. It also was created by me using a template and was entirely pink. I loved the bright, happy feel of it but worried it might not appeal as much to potential clients who have sons. Therefore, I need a site which will appeal to both genders while still keeping the cheerful color scheme of my new logo, which has pinks, blue, green and cream.
Updates

Reason: Hello! I am still trying to download my new logo and am sorry it is taking me so long. Hopefully I will it posted by the end of today (US Eastern Standard Time). Thank you all very much for your patience!

Hello! I have finally managed to upload my new logo for you to use in designing my website. I'm sorry it took so long and greatly appreciate your time and creative efforts! I look forward to seeing what is submitted based on my logo design and its style/colors.

Many thanks!

Reason: As I've been traveling and posted my logo file late, I am extending my deadline. I am now back and can focus on providing more and better feedback. I appreciate your patience and submissions very much!

Reason: I need more time to provide feedback and make decisions.

Industry/Entity Type

Daycare

Colors
0192cd
33a6d7
86cae7
cadf82
fbf289
add136
e34197

```html
<!DOCTYPE html>
<html lang="en">
<head>
<meta charset="utf-8">
<title>Puddle Jump Kidscare</title>
<link rel="stylesheet" href="https://fonts.googleapis.com/css2?family=Signika:wght@400;600&family=Source+Sans+3:wght@300;400;600;700&display=swap">
<style>
:root{
  --green:#8cc63f;
  --green-dark:#78b335;
  --green-light:#b8d65a;
  --pink:#e34197;
  --pink-soft:#f49ac1;
  --teal:#93d3d8;
  --teal-text:#5cc2c8;
  --crimson:#dd3a68;
  --brown:#6e5443;
  --grey:#7d8b8f;
  --link:#33a6d7;
  --page:#f5f9f9;
  --footer:#f3f3ef;
}
*{margin:0;padding:0;box-sizing:border-box}
html,body{width:1024px;height:1200px;overflow:hidden;background:var(--page)}
body{position:relative;font-family:"Source Sans 3",sans-serif;color:var(--grey)}
.abs{position:absolute}

.header{left:0;top:0;width:1024px;height:117px;background:var(--green)}
.brand-box{left:136px;top:0;width:154px;height:133px;background:#fff;box-shadow:0 1px 3px rgba(0,0,0,.12);z-index:5;display:flex;flex-direction:column;align-items:center;justify-content:center;gap:6px}
.brand-dot{width:22px;height:22px;border-radius:50%;background:var(--pink)}
.brand-name{font-family:"Signika",sans-serif;font-weight:600;color:var(--pink);font-size:19px;line-height:20px;text-align:center}

.topinfo{top:11px;height:30px;display:flex;align-items:center;gap:7px;color:#fff;font-size:10.5px;padding-left:14px;border-left:1px solid rgba(255,255,255,.25)}
.topinfo svg{width:14px;height:14px}
.nav{top:58px;left:300px;width:620px;height:50px}
.nav-item{position:absolute;top:0;transform:translateX(-50%);display:flex;flex-direction:column;align-items:center;color:#fff;font-size:11.5px;gap:6px;opacity:.95}
.nav-item svg{width:20px;height:20px;opacity:.55}
.nav-item.active svg{opacity:1}
.nav-pointer{left:331px;top:107px;width:0;height:0;border-left:8px solid transparent;border-right:8px solid transparent;border-bottom:10px solid #fff}

.hero{left:0;top:117px;width:1024px;height:465px;background:linear-gradient(90deg,#f7f7f6 0%,#f3f0ec 30%,#e9d2bd 55%,#d9a889 75%,#c58a6c 100%)}
.hero-tag{left:132px;top:214px;width:368px;height:216px;background:var(--teal);border-radius:34px 0 34px 0;padding:34px 0 0 26px;color:#fff;font-size:33px;line-height:46px;font-weight:300;letter-spacing:-.4px}
.hero-tag b{font-weight:700}

.panel{left:129px;top:490px;width:767px;height:510px;background:#fff}
.feature{top:512px;width:250px;text-align:center}
.feature .photo{width:146px;height:146px;border-radius:50%;margin:0 auto}
.feature h2{font-family:"Signika",sans-serif;font-weight:600;font-size:18.5px;margin-top:24px;letter-spacing:.3px}
.feature p{font-size:11.6px;line-height:16px;margin-top:6px}

.about-photo{left:154px;top:817px;width:111px;height:152px;background:linear-gradient(160deg,#9fd3ef,#f6d05a 55%,#e9866d)}
.section-title{font-family:"Signika",sans-serif;font-weight:600;font-size:13.8px;color:var(--brown)}
.about-text{left:281px;top:851px;width:330px;font-size:10.2px;line-height:14.5px}
.about-text p+p{margin-top:14px}
.read-more{font-size:8px;color:var(--link);text-decoration:underline;letter-spacing:.3px}

.news{left:650px;width:240px;height:47px}
.news-date{position:absolute;left:0;top:0;width:47px;height:47px;background:var(--pink-soft);color:#fff;text-align:center}
.news-date .day{font-size:17px;line-height:20px;padding-top:7px;display:block}
.news-date .mon{font-size:7px;display:block}
.news-text{position:absolute;left:64px;top:-2px;width:175px;font-size:10.2px;line-height:16px}
.news-text a{font-size:7.5px;color:var(--link);font-weight:600;text-decoration:none}

.footer{left:0;top:1000px;width:1024px;height:165px;background:var(--footer)}
.footer-brand{left:138px;top:1036px;display:flex;align-items:center;gap:8px}
.footer-brand .brand-name{font-size:19px;text-align:left}
.fcol{top:1032px}
.fcol h3{font-family:"Signika",sans-serif;font-weight:600;font-size:10.5px;color:var(--brown);margin-bottom:11px}
.fcol ul{list-style:none}
.fcol li{font-size:9.8px;line-height:19px;letter-spacing:.4px;padding-left:12px;position:relative}
.fcol li::before{content:"";position:absolute;left:0;top:7px;border-left:3px solid #c8c8c2;border-top:2.5px solid transparent;border-bottom:2.5px solid transparent}
.fcol li.current{color:var(--green-dark)}
.contact-row{display:flex;gap:10px;font-size:9.6px;line-height:19px;margin-bottom:5px}
.contact-row svg{width:10px;height:10px;margin-top:4px;flex:none}
.map{left:714px;top:1054px;width:174px;height:81px;background:linear-gradient(135deg,#e7e5dd,#d6d9de 60%,#b9cde4)}

.bottom-bar{left:0;top:1165px;width:1024px;height:35px;background:var(--green-light);color:#fff;font-size:9.8px}
.bottom-bar .copy{position:absolute;left:134px;top:11px}
.bottom-bar .legal{position:absolute;right:144px;top:11px}
</style>
</head>
<body>

<header class="abs header">
  <div class="abs topinfo" style="left:442px">
    <svg viewBox="0 0 16 16" fill="none" stroke="#fff" stroke-opacity=".6" stroke-width="1.6"><circle cx="8" cy="9" r="5.5"/><path d="M8 6v3l2 1.5M2 3l2.5-2M14 3l-2.5-2"/></svg>
    (Mon - Fri) 8:00AM to 6:00PM
  </div>
  <div class="abs topinfo" style="left:634px">
    <svg viewBox="0 0 16 16" fill="none" stroke="#fff" stroke-opacity=".6" stroke-width="1.4"><rect x="2" y="3.5" width="13" height="9"/><path d="M2 3.5l6.5 5 6.5-5"/></svg>
    hello@puddlejump.example
  </div>
  <div class="abs topinfo" style="left:784px">
    <svg viewBox="0 0 16 16" fill="#fff" fill-opacity=".6"><path d="M4 1.5l2.2 3-1.4 1.6c.8 1.8 2.2 3.3 4 4.1l1.6-1.4 3 2.2-1.3 2.5C7.5 13.2 2.6 8.5 1.6 3z"/></svg>
    +(555) 014-2290
  </div>

  <nav class="abs nav">
    <div class="nav-item active" style="left:38px">
      <svg viewBox="0 0 20 20" fill="#fff"><path d="M10 2l8 7h-2.5v8.5h-4v-5h-3v5h-4V9H2z"/></svg>Home</div>
    <div class="nav-item" style="left:100px">
      <svg viewBox="0 0 20 20" fill="#fff"><circle cx="10" cy="7" r="4"/><path d="M3 18c0-4 3-6.5 7-6.5s7 2.5 7 6.5z"/></svg>About</div>
    <div class="nav-item" style="left:167px">
      <svg viewBox="0 0 20 20" fill="none" stroke="#fff" stroke-width="1.6"><path d="M2 4h6.5c.8 0 1.5.7 1.5 1.5V17c0-.8-.7-1.5-1.5-1.5H2zM18 4h-6.5c-.8 0-1.5.7-1.5 1.5V17c0-.8.7-1.5 1.5-1.5H18z"/></svg>Services</div>
    <div class="nav-item" style="left:252px">
      <svg viewBox="0 0 20 20" fill="none" stroke="#fff" stroke-width="1.8"><circle cx="10" cy="10" r="7.5"/><path d="M6.5 10l2.5 2.5 4.5-5"/></svg>Hours &amp; Fees</div>
    <div class="nav-item" style="left:335px">
      <svg viewBox="0 0 20 20" fill="#fff"><path d="M4 3h4V1.5h4V3h4v16H4z"/><path d="M7 8h6M7 11h6M7 14h6" stroke="#8cc63f" stroke-width="1.3"/></svg>Policies</div>
    <div class="nav-item" style="left:404px">
      <svg viewBox="0 0 20 20" fill="#fff"><path d="M2 6h4l1.5-2h5L14 6h4v11H2z"/><circle cx="10" cy="11" r="3" fill="#8cc63f"/></svg>Photos</div>
    <div class="nav-item" style="left:485px">
      <svg viewBox="0 0 20 20" fill="#fff"><ellipse cx="11" cy="8" rx="7.5" ry="5"/><path d="M5 11l-3 5 6-3z"/></svg>Testimonials</div>
    <div class="nav-item" style="left:568px">
      <svg viewBox="0 0 20 20" fill="#fff"><path d="M2 5h16v11H2z"/><path d="M2 5l8 6 8-6" stroke="#8cc63f" stroke-width="1.3" fill="none"/></svg>Contact</div>
  </nav>
</header>

<div class="abs brand-box">
  <span class="brand-dot"></span>
  <span class="brand-name">Puddle Jump<br>Kidscare</span>
</div>

<section class="abs hero" role="img" aria-label="Photo of three laughing toddlers playing with colourful balls in a bright playroom"></section>
<div class="abs nav-pointer"></div>
<div class="abs hero-tag">A playspace where<br>children can <b>play,</b><br><b>create, and imagine!</b></div>

<main class="abs panel"></main>

<article class="abs feature" style="left:129px">
  <div class="photo" role="img" aria-label="Photo of two young children playing with toy blocks" style="background:radial-gradient(circle at 40% 40%,#f3cfa6,#c98e57 55%,#6f8f3e)"></div>
  <h2 style="color:var(--green-dark)">LEARNING</h2>
  <p>We develop age-appropriate activities that introduce and strengthen academic and to hone their social skills.</p>
</article>
<article class="abs feature" style="left:385px">
  <div class="photo" role="img" aria-label="Photo of a child with a paint-covered hand" style="background:radial-gradient(circle at 45% 45%,#f2c6b4,#b1628e 55%,#5b6e2e)"></div>
  <h2 style="color:var(--crimson)">CREATIVITY</h2>
  <p>We offer children a wide range of creative opportunities including art projects, toddler yoga lessons, and a large selection of books and games.</p>
</article>
<article class="abs feature" style="left:641px">
  <div class="photo" role="img" aria-label="Photo of a mother and daughter sharing a pretend tea party" style="background:radial-gradient(circle at 50% 40%,#f6e2cf,#d8a98a 55%,#8c6852)"></div>
  <h2 style="color:var(--teal-text)">SHARING</h2>
  <p>We strive to include enrichment activities that extend your child's understanding of the world and their role in it.</p>
</article>

<div class="abs about-photo" role="img" aria-label="Photo of children drawing at a table with a caregiver"></div>
<h2 class="abs section-title" style="left:281px;top:815px">About Puddle Jump Kidscare</h2>
<div class="abs about-text">
  <p>We are a few blocks from the 6 line subway and the 79th Street bus route, and we offer flexible hourly childcare, making it as easy as possible for busy parents on the go to arrange their children's care.</p>
  <p>We invite you to learn more about us and hope you will visit us soon</p>
  <p><span class="read-more">READ MORE</span></p>
</div>

<h2 class="abs section-title" style="left:650px;top:814px">Latest News</h2>
<div class="abs news" style="top:849px">
  <div class="news-date"><span class="day">05</span><span class="mon">May 2014</span></div>
  <p class="news-text">We are thrilled to have found a new cheerful space with a private backyard... <a>&#9656;READ MORE</a></p>
</div>
<div class="abs news" style="top:922px">
  <div class="news-date"><span class="day">05</span><span class="mon">May 2014</span></div>
  <p class="news-text">We are thrilled to have found a new cheerful space with a private backyard... <a>&#9656;READ MORE</a></p>
</div>

<footer class="abs footer"></footer>
<div class="abs footer-brand">
  <span class="brand-dot"></span>
  <span class="brand-name">Puddle Jump<br>Kidscare</span>
</div>

<div class="abs fcol" style="left:312px">
  <h3>Navigation</h3>
  <ul><li class="current">Home</li><li>About</li><li>Services</li><li>Contact</li></ul>
</div>
<div class="abs fcol" style="left:438px">
  <h3>Links</h3>
  <ul><li>Hours &amp; Fees</li><li>Policies</li><li>Testimonials</li><li>Photos</li></ul>
</div>
<div class="abs fcol" style="left:566px">
  <h3>Contact Us</h3>
  <div class="contact-row"><svg viewBox="0 0 16 16" fill="#c3c3bd"><path d="M4 1.5l2.2 3-1.4 1.6c.8 1.8 2.2 3.3 4 4.1l1.6-1.4 3 2.2-1.3 2.5C7.5 13.2 2.6 8.5 1.6 3z"/></svg>+1800-123-4567</div>
  <div class="contact-row"><svg viewBox="0 0 16 16" fill="#c3c3bd"><rect x="1" y="3" width="14" height="10"/></svg>info@yourwebsite.com</div>
  <div class="contact-row"><svg viewBox="0 0 16 16" fill="#c3c3bd"><path d="M8 1a5 5 0 0 1 5 5c0 4-5 9-5 9S3 10 3 6a5 5 0 0 1 5-5z"/></svg><span>Address, Your Country<br>Your Zip Code</span></div>
</div>
<div class="abs fcol" style="left:715px">
  <h3>Visit Us</h3>
</div>
<div class="abs map" role="img" aria-label="Street map showing the daycare location"></div>

<div class="abs bottom-bar">
  <span class="copy">Copyright 2014 © Puddle Jump Kidscare - All Rights Reserved</span>
  <span class="legal">Site Map &nbsp;&nbsp;•&nbsp;&nbsp; Privacy Policy</span>
</div>

</body>
</html>
```